- Redesign our business card
- Logo remains unchanged
- Current business card attached

Target Market(s)

We are a property management company

Industry/Entity Type

Business

```html
<!DOCTYPE html>
<html lang="en">
<head>
<meta charset="utf-8">
<title>Kestrel Property Group – Business Card</title>
<link rel="stylesheet" href="https://fonts.googleapis.com/css2?family=Roboto:wght@400;500;700&display=swap">
<style>
  :root {
    --olive: #727a40;
    --olive-strip: #6e743f;
    --card-white: #ffffff;
    --ink: #1f1f1f;
    --ink-soft: #333333;
    --sand: #d2c69a;
    --bg-green: #4b6120;
    --bg-dark: #1f1b17;
  }
  html, body {
    margin: 0;
    padding: 0;
    overflow: hidden;
  }
  .canvas {
    position: relative;
    width: 1200px;
    height: 1200px;
    overflow: hidden;
    background: linear-gradient(135deg, var(--bg-green) 0%, #2f3a1a 35%, var(--bg-dark) 65%, var(--bg-dark) 100%);
    font-family: "Roboto", Arial, sans-serif;
  }

  /* Front card */
  .card-front {
    position: absolute;
    left: 72px;
    top: 142px;
    width: 795px;
    height: 442px;
    background: var(--card-white);
    border-radius: 30px;
    overflow: hidden;
  }
  .web-strip {
    position: absolute;
    left: 0;
    top: 0;
    width: 52px;
    height: 100%;
    background: var(--olive-strip);
  }
  .web-strip span {
    position: absolute;
    left: 50%;
    bottom: 22px;
    transform-origin: left center;
    transform: translateX(8px) rotate(-90deg);
    color: var(--card-white);
    font-size: 15px;
    font-weight: 700;
    white-space: nowrap;
  }
  .holder {
    position: absolute;
    right: 512px;
    top: 108px;
    text-align: right;
  }
  .holder-name {
    margin: 0;
    font-size: 23px;
    font-weight: 500;
    color: var(--ink);
  }
  .holder-role {
    margin: 6px 0 0;
    font-size: 17px;
    color: var(--ink-soft);
  }
  .brand-band {
    position: absolute;
    left: 310px;
    top: 44px;
    right: 0;
    height: 195px;
    background: var(--olive);
    border-radius: 15px 0 0 15px;
  }
  .brand {
    position: absolute;
    color: var(--card-white);
  }
  .brand-band .brand {
    left: 46px;
    top: 108px;
  }
  .brand-name {
    display: flex;
    align-items: center;
    gap: 10px;
    margin: 0;
    font-weight: 500;
    white-space: nowrap;
  }
  .brand-mark {
    display: inline-block;
    background: var(--sand);
  }
  .brand-band .brand-name { font-size: 18px; }
  .brand-band .brand-mark { width: 14px; height: 14px; }
  .brand-band .brand-tag {
    margin: 4px 0 0 24px;
    font-size: 12px;
    letter-spacing: 0.3px;
  }
  .address {
    position: absolute;
    left: 354px;
    top: 250px;
    margin: 0;
    font-size: 18px;
    line-height: 25px;
    color: var(--ink);
    font-style: normal;
  }
  .contacts {
    position: absolute;
    left: 354px;
    top: 318px;
    margin: 0;
    padding: 0;
    list-style: none;
    font-size: 18px;
    color: var(--ink);
  }
  .contacts li {
    display: flex;
    align-items: center;
    height: 25.5px;
  }
  .contact-icon {
    display: inline-flex;
    align-items: flex-end;
    justify-content: flex-end;
    width: 14px;
    height: 14px;
    margin-right: 22px;
    background: var(--olive);
    color: var(--card-white);
    font-size: 10px;
    font-weight: 700;
    line-height: 1;
  }

  /* Back card */
  .card-back {
    position: absolute;
    left: 333px;
    top: 615px;
    width: 795px;
    height: 441px;
    background: var(--olive);
    border-radius: 30px;
  }
  .card-back .brand {
    left: 220px;
    top: 250px;
  }
  .card-back .brand-name { font-size: 27px; }
  .card-back .brand-mark { width: 20px; height: 20px; }
  .card-back .brand-tag {
    margin: 6px 0 0 30px;
    font-size: 18px;
    letter-spacing: 0.4px;
  }
  .services {
    position: absolute;
    left: 0;
    right: 0;
    top: 378px;
    margin: 0;
    text-align: center;
    color: var(--card-white);
    font-size: 17px;
    font-weight: 500;
  }
  .services .sep { margin: 0 8px; }
</style>
</head>
<body>
<div class="canvas">

  <section class="card-front">
    <div class="web-strip"><span>www.kestrelproperty.com.au</span></div>

    <div class="holder">
      <p class="holder-name">Daniel Harrow</p>
      <p class="holder-role">Licensed Strata Manager</p>
    </div>

    <div class="brand-band">
      <div class="brand">
        <p class="brand-name"><span class="brand-mark"></span>KESTREL PROPERTY GROUP</p>
        <p class="brand-tag">STRATA MANAGEMENT SERVICES</p>
      </div>
    </div>

    <address class="address">
      PO Box 48, Redfern Hills NSW 2016<br>
      12/5-19 Marlow Street Glenmore NSW 2021
    </address>

    <ul class="contacts">
      <li><span class="contact-icon">T</span>02 9000 1472</li>
      <li><span class="contact-icon">F</span>02 9000 1473</li>
      <li><span class="contact-icon">M</span>0400 318 926</li>
      <li><span class="contact-icon">E</span>info@kestrelproperty.com.au</li>
    </ul>
  </section>

  <section class="card-back">
    <div class="brand">
      <p class="brand-name"><span class="brand-mark"></span>KESTREL PROPERTY GROUP</p>
      <p class="brand-tag">STRATA MANAGEMENT SERVICES</p>
    </div>
    <p class="services">Strata Management<span class="sep">|</span>Community Management<span class="sep">|</span>Property Management</p>
  </section>

</div>
</body>
</html>
```